Business card design Needed for new logo / Construction business, home extensions and new builds

We need a business card design using our new logo files which i will attach to this project :)

We are a small construction business specialising in home extensions, new builds and property development. We are very ambitious and would appreciate professional and elegant designs for our new business card.

Very serious about using the services on MakerQuarry and recently acquired our new logo from here :)

Please get involved, i will feedback when i can as i am very busy but can respond daily, thanks

Target Market(s)

People that want to build onto their houses, new building developments or adding too their existing property

Industry/Entity Type

Construction

Contact Information for Business Card

Renwick Tolliver Construction, Lionel Ashby (Managing Director), Tel 07822254961, email - info@renwick-tolliver, www.renwick-tolliver.co.uk

Colors

Designer to choose colors to be used in the design.

Requirements
Must have
• I like a deep grey on the back please. A lot of you have provided black from and back, try mixing things up a little. The black looks cool 😎 Thanks

```html
<!DOCTYPE html>
<html lang="en">
<head>
<meta charset="utf-8">
<title>Renwick Tolliver Construction – Business Card</title>
<link rel="stylesheet" href="https://fonts.googleapis.com/css2?family=Arimo:wght@400;700&display=swap">
<style>
  :root {
    --page-bg: #e4e2de;
    --card-bg: #2e2e2f;
    --gold: #d9a11f;
    --silver: #cfcfcf;
    --white: #f4f4f4;
    --rule: #8a8a8a;
  }
  * { box-sizing: border-box; margin: 0; padding: 0; }
  html, body {
    width: 1200px;
    height: 912px;
    overflow: hidden;
    background: var(--page-bg);
    font-family: "Arimo", Arial, sans-serif;
  }
  .canvas { position: relative; width: 1200px; height: 912px; }
  .card {
    position: absolute;
    width: 580px;
    height: 331px;
    background: var(--card-bg);
    box-shadow: 0 6px 18px rgba(0,0,0,0.25);
  }
  /* Front */
  .card--front { left: 60px; top: 90px; }
  .brand-mark {
    position: absolute;
    left: 0; right: 0; top: 92px;
    display: flex; flex-direction: column; align-items: center; gap: 12px;
  }
  .brand-mark__square { width: 22px; height: 22px; background: var(--gold); }
  .brand-mark__name {
    color: var(--gold);
    font-weight: 700;
    font-size: 26px;
    letter-spacing: 1px;
    text-transform: uppercase;
    text-align: center;
    line-height: 1.15;
  }
  .front-web {
    position: absolute;
    left: 0; right: 0; bottom: 58px;
    text-align: center;
    color: var(--white);
    font-size: 16px;
    letter-spacing: 3.5px;
  }
  /* Back */
  .card--back { left: 560px; top: 480px; }
  .back-brand {
    position: absolute;
    right: 44px; top: 36px;
    display: flex; align-items: center; gap: 10px;
  }
  .back-brand__square { width: 14px; height: 14px; background: var(--gold); }
  .back-brand__name {
    color: var(--silver);
    font-weight: 400;
    font-size: 17px;
    letter-spacing: 0.5px;
    text-transform: uppercase;
  }
  .back-web {
    position: absolute;
    right: 40px; top: 148px;
    color: var(--white);
    font-size: 13px;
  }
  .back-rule {
    position: absolute;
    left: 200px; right: 40px; top: 170px;
    height: 1px; background: var(--rule);
  }
  .contact {
    position: absolute;
    left: 40px; top: 210px;
  }
  .contact__name { color: var(--gold); font-weight: 700; font-size: 24px; }
  .contact__title { color: var(--silver); font-size: 15px; margin-top: 2px; }
  .contact__rule { width: 170px; height: 1px; background: var(--rule); margin: 10px 0 8px; }
  .contact__line {
    display: flex; align-items: center; gap: 8px;
    color: var(--white); font-size: 15px; line-height: 21px;
  }
  .contact__line svg { width: 13px; height: 13px; flex: none; }
</style>
</head>
<body>
<main class="canvas">

  <section class="card card--front" aria-label="Card front">
    <div class="brand-mark">
      <span class="brand-mark__square"></span>
      <span class="brand-mark__name">Renwick Tolliver<br>Construction</span>
    </div>
    <p class="front-web">www.renwick-tolliver.co.uk</p>
  </section>

  <section class="card card--back" aria-label="Card back">
    <div class="back-brand">
      <span class="back-brand__square"></span>
      <span class="back-brand__name">Renwick Tolliver Construction</span>
    </div>
    <p class="back-web">www.renwick-tolliver.co.uk</p>
    <div class="back-rule"></div>

    <div class="contact">
      <p class="contact__name">Lionel Ashby</p>
      <p class="contact__title">Managing Director</p>
      <div class="contact__rule"></div>
      <p class="contact__line">
        <svg viewBox="0 0 16 16" aria-hidden="true"><path fill="var(--gold)" d="M3.6 1.2l2.3 2.6-1.2 1.8c.9 2 2.6 3.7 4.6 4.6l1.8-1.2 2.6 2.3-1.4 2.4C7.2 13.6 2.4 8.8 1.2 3z"/></svg>
        07822254961
      </p>
      <p class="contact__line">
        <svg viewBox="0 0 16 16" aria-hidden="true"><rect x="1" y="3" width="14" height="10" fill="var(--gold)"/><path d="M1.5 3.5L8 9l6.5-5.5" fill="none" stroke="var(--card-bg)" stroke-width="1.3"/></svg>
        info@renwick-tolliver
      </p>
    </div>
  </section>

</main>
</body>
</html>
```